Flyer Design Project

I need a cool design that describes a new line of services I am selling. The final product should be a 8 1/2 by 11 and maximum two pages.

I am selling consulting services to learn to use web conferencing tools for business development, meeting and training.
Updates

Please use the file I have attached as a guide for your work. It is a document called "guide-quickofficehints" and I love its design.

Thanks

                                        Please substitute the new text availble and just uploaded in the FLYER. Please submit the FINAL version fo your design with TExt changes as well as improvements detailed in previous message. 

Target Market(s)

Entrepreneurs and classroom educators who wnats to explore a new way to teach (innovators not scared of technology)

Industry/Entity Type

Business

Requirements
Must have
• I would like to receive a final PDF with the content EDITABLE for minor edits (I have acrobat)
Logo should be included (attached)

PLEASE CHECK OUT ATTACHED DOCUMENT WHOSE DESIGN I LOVE.
IT is called "Guide quick-office hints". If you could follow that as a template to design mine that would be great!

```html
<!DOCTYPE html>
<html lang="en">
<head>
<meta charset="utf-8">
<title>Convenelab Consulting – Online Engagement Services</title>
<link href="https://fonts.googleapis.com/css2?family=Arimo:wght@400;700&display=swap" rel="stylesheet">
<style>
  :root {
    --orange: #f47920;
    --orange-line: #f58a3a;
    --ink: #222222;
    --brand-ink: #1e1e1e;
    --arrow: #8a4a1c;
    --bar-1: #fbc315;
    --bar-2: #f7a21b;
    --bar-3: #f47f20;
    --bar-4: #f05a24;
    --bar-5: #e52421;
    --bar-6: #c1191e;
    --bar-7: #9b1111;
    --tint-1: #fff5dc;
    --tint-2: #fff0da;
    --tint-3: #fee9d6;
    --tint-4: #fde3d2;
    --tint-5: #fcdccd;
    --tint-6: #f7d7cb;
    --tint-7: #f0d0c4;
  }
  * { box-sizing: border-box; margin: 0; padding: 0; }
  html, body { width: 849px; height: 1200px; overflow: hidden; background: #fff; }
  body { font-family: "Arimo", Arial, sans-serif; color: var(--ink); }
  .flyer { position: relative; width: 849px; height: 1200px; overflow: hidden; background: #fff; }
  .flyer-frame { position: absolute; inset: 0; }

  .brand {
    position: absolute; top: 48px; right: 40px; text-align: right;
    font-size: 22px; font-weight: 700; line-height: 26px; color: var(--brand-ink);
    letter-spacing: 1px;
  }

  .headline {
    position: absolute; left: 236px; top: 142px; width: 480px;
    font-size: 22px; font-weight: 700; line-height: 30.8px; color: var(--orange);
  }

  .services { position: absolute; left: 233px; top: 242px; width: 576px; list-style: none; }
  .service {
    position: relative; margin-bottom: 2px; padding: 9px 21px 8px 40px;
    border-top: 1px solid var(--orange-line); border-radius: 6px 0 0 6px;
    font-size: 13.6px; line-height: 18.5px; text-align: justify; overflow: hidden;
  }
  .service::before {
    content: ""; position: absolute; left: 0; top: 0; bottom: 0; width: 13px; background: var(--bar);
  }
  .service-arrow { position: absolute; left: 22px; top: 13px; width: 12px; height: 10px; }
  .service-1 { --bar: var(--bar-1); background: var(--tint-1); height: 134px; }
  .service-2 { --bar: var(--bar-2); background: var(--tint-2); height: 112px; }
  .service-3 { --bar: var(--bar-3); background: var(--tint-3); height: 92px; }
  .service-4 { --bar: var(--bar-4); background: var(--tint-4); height: 93px; }
  .service-5 { --bar: var(--bar-5); background: var(--tint-5); height: 93px; }
  .service-6 { --bar: var(--bar-6); background: var(--tint-6); height: 71px; }
  .service-7 { --bar: var(--bar-7); background: var(--tint-7); height: 71px; }

  .intro {
    position: absolute; left: 233px; top: 933px; width: 576px;
    font-size: 13.6px; line-height: 18.5px; text-align: justify; hyphens: auto;
  }

  .call-to-action {
    position: absolute; right: 38px; top: 1133px; color: #fff; font-size: 17.5px;
  }
  .call-to-action strong { font-weight: 700; }
  .call-to-action .phone { font-size: 26px; font-weight: 700; }
</style>
</head>
<body>
<main class="flyer">
  <svg class="flyer-frame" width="849" height="1200" viewBox="0 0 849 1200" aria-hidden="true">
    <line x1="205" y1="125" x2="849" y2="125" stroke="var(--orange-line)" stroke-width="1.5"/>
    <path d="M236 0 C 110 250, 40 560, 95 820 S 135 1080, 150 1118" fill="none" stroke="var(--orange)" stroke-width="1.5"/>
    <path d="M150 1117 L849 1117 L849 1200 L185 1200 C 172 1175, 160 1148, 150 1117 Z" fill="var(--orange)"/>
  </svg>

  <header class="brand">
    <div>CONVENELAB</div>
    <div>CONSULTING</div>
  </header>

  <h1 class="headline">Choose the service that best fit your needs and budget. A new level of online engagement and virtual collaboration awaits.</h1>

  <ul class="services">
    <li class="service service-1"><svg class="service-arrow" viewBox="0 0 12 10"><path d="M1 1 Q1 6 6 6 L6 9 L11 5 L6 1 L6 4 Q3 4 1 1Z" fill="var(--arrow)"/></svg>Webinar Series: Plan, design, develop and implement a 3+1 session webinar series about the content of your expertise marketed to live audiences with 3 hours of One-on-One online coaching on web conferencing tools and how to use them for your business. Includes access to online resource library of our Online Facilitator Certification plus access to your own online meeting room and virtual collaboration platform ($3,000).</li>
    <li class="service service-2"><svg class="service-arrow" viewBox="0 0 12 10"><path d="M1 1 Q1 6 6 6 L6 9 L11 5 L6 1 L6 4 Q3 4 1 1Z" fill="var(--arrow)"/></svg>Webinar: Plan, design, develop and implement 1 webinar session on the content of your expertise marketed to live audiences with 3 hours of One-on-One online coaching on web conferencing tools and how to use them for your business. Includes access to online resource library of our Online Facilitator Certification plus access to your own online meeting room and virtual collaboration platform ($1,900).</li>
    <li class="service service-3"><svg class="service-arrow" viewBox="0 0 12 10"><path d="M1 1 Q1 6 6 6 L6 9 L11 5 L6 1 L6 4 Q3 4 1 1Z" fill="var(--arrow)"/></svg>Outfitting the Online Entrepreneur: 4-hours of One-on-One online coaching to learn about web conferencing tools and how to use them for your business. Includes access to online resource library of our Online Facilitator Certification plus access to your own online meeting room and virtual collaboration platform ($1,300).</li>
    <li class="service service-4"><svg class="service-arrow" viewBox="0 0 12 10"><path d="M1 1 Q1 6 6 6 L6 9 L11 5 L6 1 L6 4 Q3 4 1 1Z" fill="var(--arrow)"/></svg>Outfitting the Online Educator: 3-hours of One-on-One online coaching to learn about web conferencing tools and how to use them for your training sessions. Includes access to online resource library of our Online Facilitator Certification plus access to your own online meeting room and virtual collaboration platform ($1,200).</li>
    <li class="service service-5"><svg class="service-arrow" viewBox="0 0 12 10"><path d="M1 1 Q1 6 6 6 L6 9 L11 5 L6 1 L6 4 Q3 4 1 1Z" fill="var(--arrow)"/></svg>Repurposing for Online Audiences: Design and develop materials, agenda, event plans and activities to repurpose your face-to-face session for online sessions that market your expertise. Includes 2-hours of One-on-One online coaching to learn about web conferencing tools and how to use them for your business ($500).</li>
    <li class="service service-6"><svg class="service-arrow" viewBox="0 0 12 10"><path d="M1 1 Q1 6 6 6 L6 9 L11 5 L6 1 L6 4 Q3 4 1 1Z" fill="var(--arrow)"/></svg>One-on-one coaching with resources: 2-hours of One-on-One online coaching to learn about web conferencing tools and how to use them for your business. Includes access to online resource library of our Online Facilitator Certification ($300).</li>
    <li class="service service-7"><svg class="service-arrow" viewBox="0 0 12 10"><path d="M1 1 Q1 6 6 6 L6 9 L11 5 L6 1 L6 4 Q3 4 1 1Z" fill="var(--arrow)"/></svg>One-on-one coaching: 2-hours of One-on-One online coaching to learn about web conferencing tools and how to use them for your business. Includes three job aids for online facilitators ($200)</li>
  </ul>

  <section class="intro">
    <p>You'll participate via the BrightRoom Connect Meeting platform. No special software is required. If you have a computer with Internet access and a direct telephone line you have all is needed to participate.</p>
    <p>As a professional communicators – whether you are a small business owner, an educator or a manager - you know that webinar technology is here to stay. Have you wondered how to use them to benefit your business or your organization? Leave the details to us. Well implemented online sessions can give your business unparalleled access to new markets and potential new clients at a minimum cost.</p>
  </section>

  <footer class="call-to-action">Want to know more? <strong>Call us at</strong> <span class="phone">555-0142-7788</span></footer>
</main>
</body>
</html>
```